BOLD & MINIMALIST DESIGN NEEDED

We want a very bold but minimalistic business card design that is impactful and utilizes both sides of the business card. Our current logo is included for your use.

We want bold fonts and good use of negative space. We don't want the logo to overpower the design.

Target Market(s)

Professionals who are building new commercial buildings.

Industry/Entity Type

Construction

Contact Information for Business Card

Name, Title, email, office phone, cell phone, website

Font styles to use
Serif
Sans Serif

Requirements
Must have
• Bold design!

```html
<!DOCTYPE html>
<html lang="en">
<head>
<meta charset="utf-8">
<title>Ridgeline Build Co. – Stationery Set 3</title>
<link href="https://fonts.googleapis.com/css2?family=Josefin+Sans:wght@400;700&family=Open+Sans:wght@400&display=swap" rel="stylesheet">
<style>
  :root {
    --board: #1e2021;
    --board-light: #2b2e2f;
    --paper: #ffffff;
    --ink: #111111;
    --muted: #444444;
    --green: #7cc242;
    --rule: #b9b9b9;
    --label: #f2f2f2;
  }
  * { box-sizing: border-box; margin: 0; padding: 0; }
  html, body { width: 953px; height: 1200px; overflow: hidden; }
  body {
    position: relative;
    background: radial-gradient(ellipse at 50% 40%, var(--board-light), var(--board) 70%);
    font-family: "Josefin Sans", sans-serif;
    color: var(--ink);
  }
  .label {
    position: absolute;
    font-family: "Open Sans", sans-serif;
    font-size: 17px;
    color: var(--label);
  }
  .sheet { position: absolute; background: var(--paper); overflow: hidden; }

  .brand {
    font-family: "Josefin Sans", sans-serif;
    font-weight: 700;
    color: var(--ink);
    line-height: 1.05;
    text-align: center;
    font-size: 12px;
    letter-spacing: 0.02em;
  }

  .head { position: absolute; display: flex; align-items: center; }
  .head .brand { width: 82px; }
  .divider { width: 1px; background: var(--green); align-self: stretch; margin: 0 8px; }
  .contacts { list-style: none; font-size: 6.6px; color: var(--muted); line-height: 1.65; }
  .contacts li { display: flex; align-items: flex-start; gap: 4px; }
  .contacts svg { width: 6px; height: 6px; margin-top: 1px; flex: none; fill: var(--ink); }

  /* business cards */
  .card { position: absolute; width: 300px; height: 171px; background: var(--paper); border-radius: 12px; }
  .card-front { left: 122px; top: 128px; display: flex; align-items: center; justify-content: center; }
  .card-front .brand { font-size: 22px; width: 180px; }
  .card-back { left: 122px; top: 314px; }
  .card-back .brand { position: absolute; left: 22px; top: 30px; font-size: 15px; width: 100px; }
  .person { position: absolute; right: 132px; top: 64px; text-align: right; }
  .person .role { font-size: 8px; color: var(--muted); }
  .person .name { font-size: 11px; font-weight: 700; }
  .card-back .divider-abs { position: absolute; left: 176px; top: 36px; width: 1px; height: 80px; background: var(--green); }
  .card-back .contacts { position: absolute; left: 184px; top: 36px; font-size: 7.4px; }

  .lines { position: absolute; left: 13px; right: 13px; top: 102px; }
  .lines span { display: block; height: 16.5px; border-top: 1px solid var(--rule); }

  .compliments { position: absolute; left: 14px; bottom: 14px; color: var(--green); font-weight: 700; font-size: 13px; letter-spacing: 0.03em; }

  .flap { position: absolute; left: 0; top: 0; width: 100%; height: 70px; }
</style>
</head>
<body>

  <div class="label" style="left:77px; top:58px;">Business card_3</div>
  <div class="card card-front">
    <div class="brand">RIDGELINE BUILD CO.</div>
  </div>
  <div class="card card-back">
    <div class="brand">RIDGELINE BUILD CO.</div>
    <div class="person">
      <div class="role">Founder</div>
      <div class="name">Jordan Ellery</div>
    </div>
    <div class="divider-abs"></div>
    <ul class="contacts">
      <li><svg viewBox="0 0 10 10"><rect x="2.5" y="0.5" width="5" height="9" rx="1" fill="none" stroke="#111"/></svg>3XX-2XX-9XXX</li>
      <li><svg viewBox="0 0 10 10"><path d="M2 0.5 L4 3 L3 4.5 Q4.5 6.5 5.5 7 L7 6 L9.5 8 L8 9.5 Q3 9 0.5 2 Z"/></svg>555-210-4400</li>
      <li><svg viewBox="0 0 10 10"><path d="M0.5 2 H9.5 V8 H0.5 Z M0.5 2 L5 5.5 L9.5 2" fill="none" stroke="#111"/></svg>hello@ridgeline.co</li>
      <li><svg viewBox="0 0 10 10"><circle cx="5" cy="5" r="4.3" fill="none" stroke="#111"/><path d="M0.7 5 H9.3 M5 0.7 V9.3" stroke="#111"/></svg>www.ridgeline.co</li>
      <li><svg viewBox="0 0 10 10"><path d="M5 0.5 A3.5 3.5 0 0 1 8.5 4 Q8.5 6 5 9.5 Q1.5 6 1.5 4 A3.5 3.5 0 0 1 5 0.5 Z"/></svg>1420 Cedar Hollow Rd.<br>Pine Gap, GA 30000</li>
    </ul>
  </div>

  <div class="label" style="left:499px; top:58px;">Letterhead_3</div>
  <div class="sheet letterhead" style="left:499px; top:97px; width:377px; height:488px;">
    <div class="head" style="left:12px; top:14px;">
      <div class="brand">RIDGELINE BUILD CO.</div>
      <div class="divider"></div>
      <ul class="contacts">
        <li><svg viewBox="0 0 10 10"><path d="M2 0.5 L4 3 L3 4.5 Q4.5 6.5 5.5 7 L7 6 L9.5 8 L8 9.5 Q3 9 0.5 2 Z"/></svg>555-210-4400</li>
        <li><svg viewBox="0 0 10 10"><path d="M0.5 2 H9.5 V8 H0.5 Z M0.5 2 L5 5.5 L9.5 2" fill="none" stroke="#111"/></svg>hello@ridgeline.co</li>
        <li><svg viewBox="0 0 10 10"><circle cx="5" cy="5" r="4.3" fill="none" stroke="#111"/><path d="M0.7 5 H9.3 M5 0.7 V9.3" stroke="#111"/></svg>www.ridgeline.co</li>
        <li><svg viewBox="0 0 10 10"><path d="M5 0.5 A3.5 3.5 0 0 1 8.5 4 Q8.5 6 5 9.5 Q1.5 6 1.5 4 A3.5 3.5 0 0 1 5 0.5 Z"/></svg>1420 Cedar Hollow Rd.<br>Pine Gap, GA 30000</li>
      </ul>
    </div>
  </div>

  <div class="label" style="left:77px; top:582px;">Note Pads_3</div>
  <div class="sheet notepad" style="left:77px; top:619px; width:360px; height:253px;">
    <div class="head" style="left:14px; top:14px;">
      <div class="brand">RIDGELINE BUILD CO.</div>
      <div class="divider"></div>
      <ul class="contacts">
        <li><svg viewBox="0 0 10 10"><path d="M2 0.5 L4 3 L3 4.5 Q4.5 6.5 5.5 7 L7 6 L9.5 8 L8 9.5 Q3 9 0.5 2 Z"/></svg>555-210-4400</li>
        <li><svg viewBox="0 0 10 10"><path d="M0.5 2 H9.5 V8 H0.5 Z M0.5 2 L5 5.5 L9.5 2" fill="none" stroke="#111"/></svg>hello@ridgeline.co</li>
        <li><svg viewBox="0 0 10 10"><circle cx="5" cy="5" r="4.3" fill="none" stroke="#111"/><path d="M0.7 5 H9.3 M5 0.7 V9.3" stroke="#111"/></svg>www.ridgeline.co</li>
        <li><svg viewBox="0 0 10 10"><path d="M5 0.5 A3.5 3.5 0 0 1 8.5 4 Q8.5 6 5 9.5 Q1.5 6 1.5 4 A3.5 3.5 0 0 1 5 0.5 Z"/></svg>1420 Cedar Hollow Rd.<br>Pine Gap, GA 30000</li>
      </ul>
    </div>
    <div class="lines"><span></span><span></span><span></span><span></span><span></span><span></span><span></span><span></span></div>
  </div>

  <div class="label" style="left:492px; top:652px;">Comp Slips_3</div>
  <div class="sheet compslip" style="left:492px; top:691px; width:384px; height:181px;">
    <div class="head" style="left:12px; top:14px;">
      <div class="brand">RIDGELINE BUILD CO.</div>
      <div class="divider"></div>
      <ul class="contacts">
        <li><svg viewBox="0 0 10 10"><path d="M2 0.5 L4 3 L3 4.5 Q4.5 6.5 5.5 7 L7 6 L9.5 8 L8 9.5 Q3 9 0.5 2 Z"/></svg>555-210-4400</li>
        <li><svg viewBox="0 0 10 10"><path d="M0.5 2 H9.5 V8 H0.5 Z M0.5 2 L5 5.5 L9.5 2" fill="none" stroke="#111"/></svg>hello@ridgeline.co</li>
        <li><svg viewBox="0 0 10 10"><circle cx="5" cy="5" r="4.3" fill="none" stroke="#111"/><path d="M0.7 5 H9.3 M5 0.7 V9.3" stroke="#111"/></svg>www.ridgeline.co</li>
        <li><svg viewBox="0 0 10 10"><path d="M5 0.5 A3.5 3.5 0 0 1 8.5 4 Q8.5 6 5 9.5 Q1.5 6 1.5 4 A3.5 3.5 0 0 1 5 0.5 Z"/></svg>1420 Cedar Hollow Rd.<br>Pine Gap, GA 30000</li>
      </ul>
    </div>
    <div class="compliments">With Compliments</div>
  </div>

  <div class="label" style="left:77px; top:912px;">ENV Front_3</div>
  <div class="sheet envelope-front" style="left:77px; top:951px; width:388px; height:169px;">
    <div class="head" style="left:12px; top:14px;">
      <div class="brand">RIDGELINE BUILD CO.</div>
      <div class="divider"></div>
      <ul class="contacts">
        <li><svg viewBox="0 0 10 10"><path d="M5 0.5 A3.5 3.5 0 0 1 8.5 4 Q8.5 6 5 9.5 Q1.5 6 1.5 4 A3.5 3.5 0 0 1 5 0.5 Z"/></svg>1420 Cedar Hollow Rd.<br>Pine Gap, GA 30000</li>
      </ul>
    </div>
  </div>

  <div class="label" style="left:499px; top:912px;">ENV Back_3</div>
  <div class="sheet envelope-back" style="left:499px; top:951px; width:386px; height:169px;">
    <svg class="flap" viewBox="0 0 386 70" preserveAspectRatio="none">
      <path d="M0 0 H386 Q378 30 360 33 L193 62 L26 33 Q8 30 0 0 Z" fill="#060606"/>
    </svg>
  </div>

</body>
</html>
```